Podiatry clinic requires a modern revamp and editing of existing website.

I would like a fresh new look and updated information for my current business website. An easy to navigate site with prominent address and phone number for call to action. We are a podiatry clinic that focuses on general and sports podiatry.
I would like 4 pages; including Home page, About Us, Services & Contact.
www.brambleridgepodiatry.net

Target Market(s)

Active working professionals.

Industry/Entity Type

Medical

Coding

Coded - Design and coding required

Number of Pages Required

4 page

Font styles to use
Sans Serif

Colors
6b449b

Requirements
Must have
• A modern look with logo and active images; clean and uncluttered. Visible phone number and address for call to action.
• 4 pages - Home, About Us, Services, Contact.
• Home page - update address & service logos.
• About Us - update of personal information.
• Services - Revamp of existing page.
• Contact page to include Google map, email & phone number.
Nice to have
• Ability to add content easily; eg. a blog or adding video onto Home page.
• Link to Socialnook page.

```html
<!DOCTYPE html>
<html lang="en">
<head>
<meta charset="utf-8">
<title>Brambleridge Podiatry</title>
<link rel="stylesheet" href="https://fonts.googleapis.com/css2?family=Source+Sans+3:ital,wght@0,400;0,600;0,700;1,700&display=swap">
<style>
:root{
  --purple:#6b449b;
  --purple-deep:#432a88;
  --purple-soft:#9b82c0;
  --orange:#f5823a;
  --page:#e6e6e6;
  --white:#ffffff;
  --text:#3a3a3a;
  --light:#f3f3f3;
  --footer:#c9c9c9;
  --line:#d6d6d6;
}
*{box-sizing:border-box;margin:0;padding:0}
html,body{width:1200px;height:2350px;overflow:hidden}
body{background:var(--page);font-family:"Source Sans 3",Arial,sans-serif;color:var(--text);position:relative}
.site{position:absolute;left:15px;top:16px;width:1170px;height:2319px;background:var(--white);overflow:hidden}
.abs{position:absolute}

/* header */
.brand{left:30px;top:38px;font-size:30px;line-height:32px;font-weight:700;color:var(--purple);display:flex;align-items:center;gap:12px}
.brand .dot{width:22px;height:22px;border-radius:50%;background:var(--purple)}
.follow{left:880px;top:16px;font-size:15px;color:#555;display:flex;align-items:center;gap:10px;font-weight:600}
.follow .sep{width:1px;height:20px;background:#bbb}
.follow .net{font-size:19px;font-weight:700;color:var(--purple-deep)}
.icon-ring{width:38px;height:38px;border:2px solid var(--purple-deep);border-radius:50%;display:flex;align-items:center;justify-content:center}
.addr{left:728px;top:74px;display:flex;gap:12px;align-items:center}
.addr p,.phone p{font-size:18px;line-height:21px;font-weight:700;color:#222}
.phone{left:965px;top:81px;display:flex;gap:12px;align-items:center}

/* nav */
.nav{left:0;top:159px;width:1170px;height:46px;background:var(--purple-soft);display:flex;justify-content:center}
.nav a{color:var(--white);text-decoration:none;font-size:15px;font-weight:700;text-transform:uppercase;padding:0 24px;line-height:46px}
.nav a.active{background:var(--purple-deep);padding:0 28px}

/* hero */
.hero{left:0;top:205px;width:1170px;height:553px;background:radial-gradient(circle at 45% 55%,#e07a3a 0,#9a5a4a 12%,#4f4f6a 30%,#30324e 60%,#4a4d6e 100%)}
.hero-copy{left:712px;top:168px;width:400px;color:var(--white)}
.hero-copy h1{font-size:27px;font-weight:700;margin-bottom:10px}
.hero-copy p{font-size:16.5px;line-height:21px}
.hero-btns{display:flex;gap:10px;margin-top:22px}
.btn{display:inline-block;background:var(--purple-soft);color:var(--white);font-size:14px;font-weight:700;text-transform:uppercase;text-align:center;text-decoration:none;line-height:34px}
.hero-btns .btn{border:2px solid var(--white);width:180px}
.arrow{top:246px;width:70px;height:48px;background:var(--purple-deep);display:flex;align-items:center;justify-content:center}

/* service cards */
.card{top:724px;width:480px;height:430px;background:linear-gradient(#fff 60%,#f2f2f2);box-shadow:0 16px 12px -12px rgba(0,0,0,.35)}
.card .photo{position:absolute;left:10px;top:10px;width:460px;height:230px}
.card p{position:absolute;left:13px;top:259px;width:450px;font-size:14px;line-height:19px}
.card .btn{position:absolute;left:150px;bottom:36px;width:180px;line-height:36px;font-size:15px}
.badge{top:708px;width:134px;height:134px;border-radius:50%;border:2px solid var(--orange);padding:5px}
.badge div{width:100%;height:100%;border-radius:50%;background:var(--orange);color:var(--white);font-size:18px;font-weight:600;line-height:20px;display:flex;align-items:center;justify-content:center;text-align:center}

/* about */
.about{left:0;top:1214px;width:1170px;height:535px;background:var(--light)}
.about h2{position:absolute;left:0;top:48px;width:1170px;text-align:center;font-size:28px;font-weight:400;color:#333}
.about h2 em{color:var(--purple-deep);font-weight:700}
.divider{position:absolute;left:95px;top:108px;width:980px;height:2px;background:var(--line)}
.divider-mark{position:absolute;left:577px;top:102px;width:14px;height:14px;border-radius:50%;background:var(--purple-deep)}
.about .body{position:absolute;left:95px;top:188px;width:985px;font-size:15.5px;line-height:21px}
.about .body p{margin-bottom:20px}
.about .body strong{color:var(--purple-deep)}
.about .btn{position:absolute;left:496px;top:440px;width:180px;line-height:36px;font-size:16px}

/* partners */
.partners{left:0;top:1749px;width:1170px;height:202px}
.partner{top:70px;height:60px;border-radius:8px;background:#e4e1ec}

/* footer */
.footer{left:0;top:1935px;width:1170px;height:349px;background:var(--footer)}
.footer .brand{left:40px;top:120px}
.col h3{font-size:16px;font-weight:700;color:var(--purple-deep);padding-bottom:10px;border-bottom:1px solid #9a9a9a;margin-bottom:18px}
.col a,.col p{display:block;font-size:14px;line-height:21px;color:#222;text-decoration:none;font-weight:600}
.contact-row{display:flex;gap:10px;margin-bottom:18px}
.map{left:733px;top:40px;width:400px;height:238px;background:linear-gradient(135deg,#efe9d8,#f4ecc9 50%,#e5e0d2)}
.copyright{left:0;top:2284px;width:1170px;height:35px;background:var(--purple-deep);color:var(--white);font-size:11px;font-weight:700;text-align:center;line-height:35px;text-transform:uppercase}
</style>
</head>
<body>
<div class="site">

  <header>
    <div class="brand abs"><span class="dot"></span><span>Brambleridge<br>Podiatry</span></div>
    <div class="follow abs"><span>Follow us on</span><span class="sep"></span><span class="net">Socialnook</span></div>
    <div class="addr abs">
      <span class="icon-ring"><svg width="16" height="20" viewBox="0 0 16 20"><path d="M8 1a7 7 0 0 0-7 7c0 5 7 11 7 11s7-6 7-11a7 7 0 0 0-7-7z" fill="none" stroke="#432a88" stroke-width="2"/><circle cx="8" cy="8" r="2.5" fill="#432a88"/></svg></span>
      <p>Suite 208<br>72 Larkspur Lane<br>Fernvale 3050</p>
    </div>
    <div class="phone abs">
      <span class="icon-ring"><svg width="18" height="18" viewBox="0 0 24 24"><path d="M6.6 10.8a15 15 0 0 0 6.6 6.6l2.2-2.2c.3-.3.7-.4 1-.2 1.1.4 2.3.6 3.6.6.6 0 1 .4 1 1V20c0 .6-.4 1-1 1A17 17 0 0 1 3 4c0-.6.4-1 1-1h3.5c.6 0 1 .4 1 1 0 1.3.2 2.5.6 3.6.1.3 0 .7-.2 1z" fill="#432a88"/></svg></span>
      <p>1300 555 274</p>
    </div>
  </header>

  <nav class="nav abs">
    <a class="active" href="#">Home</a><a href="#">About Us</a><a href="#">Services</a><a href="#">Contact</a>
  </nav>

  <section class="hero abs" role="img" aria-label="Runner on a treadmill with the foot bones highlighted in a warm glow">
    <div class="arrow abs" style="left:0"><svg width="16" height="22" viewBox="0 0 16 22"><path d="M12 2 4 11l8 9" fill="none" stroke="#fff" stroke-width="3"/></svg></div>
    <div class="arrow abs" style="left:1100px"><svg width="16" height="22" viewBox="0 0 16 22"><path d="m4 2 8 9-8 9" fill="none" stroke="#fff" stroke-width="3"/></svg></div>
    <div class="hero-copy abs">
      <h1>Welcome to Brambleridge Podiatry</h1>
      <p>We provide General Podiatry Treatment and some Specialised Services in relation to various foot conditions, including Sports Injuries, Orthotic Therapy and Nail Surgery.</p>
      <div class="hero-btns"><a class="btn" href="#">View Services</a><a class="btn" href="#">Make an Appointment</a></div>
    </div>
  </section>

  <article class="card abs" style="left:95px">
    <div class="photo" role="img" aria-label="Podiatrist treating the sole of a patient's foot with a small tool" style="background:linear-gradient(135deg,#d9cfc6,#b7a89c 50%,#e8e3de)"></div>
    <p>At Brambleridge Podiatry, we provide general treatments including; Nails, Corns, Callus, Warts, Skin Disorders, Heel Pain, Heel Spurs, Arch Pain-Plantar Fasciitis, Ankle Pain, Shin Splints, Knee Paint, Bunions, Hammestoes and Toe Deformities</p>
    <a class="btn" href="#">Learn More</a>
  </article>
  <div class="badge abs" style="left:63px"><div>General<br>Treatments</div></div>

  <article class="card abs" style="left:624px">
    <div class="photo" role="img" aria-label="Practitioner examining a patient's bare foot" style="background:linear-gradient(135deg,#e6e2de,#d2bfae 50%,#f0eeec)"></div>
    <p>Our specialised treatments including; Diabetic Management, Nail Surgery, Biomechanical Assessment, Gait Analysis, and Orthotic Therapy.</p>
    <a class="btn" href="#">Learn More</a>
  </article>
  <div class="badge abs" style="left:595px"><div>Specialised<br>Treatments</div></div>

  <section class="about abs">
    <h2>About <em>Brambleridge Podiatry</em></h2>
    <div class="divider"></div><div class="divider-mark"></div>
    <div class="body">
      <p>Brambleridge Podiatry is a Podiatry clinic in the heart of Fernvale CBD. We are located between Alder &amp; Quince Streets in the Harbourview Business Centre.</p>
      <p>Our podiatrists are fully qualified health professionals who are able to diagnose, treat, manage or help to prevent all medical conditions that affect the feet and lower limb.</p>
      <p>We provide General Podiatry Treatment and some Specialised Services in relation to various foot conditions, including Sports Injuries, Orthotic Therapy and Nail Surgery.</p>
      <p>For Appointments or Enquiries please call us on <strong>1300 555 274</strong> or email: <strong>info@brambleridgepodiatry.net</strong></p>
    </div>
    <a class="btn" href="#">More About Us</a>
  </section>

  <section class="partners abs" aria-label="Accepted schemes and memberships">
    <div class="partner abs" style="left:173px;width:216px"></div>
    <div class="partner abs" style="left:439px;width:157px"></div>
    <div class="partner abs" style="left:654px;width:144px"></div>
    <div class="partner abs" style="left:855px;width:141px"></div>
  </section>

  <footer class="footer abs">
    <div class="brand abs"><span class="dot"></span><span>Brambleridge<br>Podiatry</span></div>
    <div class="col abs" style="left:275px;top:50px;width:110px">
      <h3>Quick Links</h3>
      <a href="#">Home</a><a href="#">About Us</a><a href="#">Services</a><a href="#">Contact</a>
    </div>
    <div class="col abs" style="left:443px;top:50px;width:230px">
      <h3>Contact</h3>
      <div class="contact-row"><svg width="10" height="14" viewBox="0 0 16 20"><path d="M8 1a7 7 0 0 0-7 7c0 5 7 11 7 11s7-6 7-11a7 7 0 0 0-7-7z" fill="#432a88"/></svg><p>Brambleridge Podiatry<br>Suite 208<br>72 Larkspur Lane<br>Fernvale 3050</p></div>
      <div class="contact-row"><svg width="13" height="13" viewBox="0 0 24 24"><path d="M6.6 10.8a15 15 0 0 0 6.6 6.6l2.2-2.2c.3-.3.7-.4 1-.2 1.1.4 2.3.6 3.6.6.6 0 1 .4 1 1V20c0 .6-.4 1-1 1A17 17 0 0 1 3 4c0-.6.4-1 1-1h3.5c.6 0 1 .4 1 1 0 1.3.2 2.5.6 3.6.1.3 0 .7-.2 1z" fill="#432a88"/></svg><p>1300 555 274</p></div>
      <div class="contact-row"><svg width="14" height="12" viewBox="0 0 14 12" style="margin-top:4px"><rect x="0" y="1" width="14" height="10" fill="#432a88"/><path d="m0 1 7 6 7-6" fill="none" stroke="#c9c9c9" stroke-width="1.4"/></svg><p>info@brambleridgepodiatry.net</p></div>
      <div class="contact-row" style="align-items:center"><p>Follow us on</p><span style="width:1px;height:18px;background:#888"></span><p style="font-size:17px;font-weight:700">Socialnook</p></div>
    </div>
    <div class="map abs" role="img" aria-label="Street map showing the clinic location"></div>
  </footer>
  <div class="copyright abs">Copyright © 2016 Brambleridge Podiatry. All rights reserved.</div>

</div>
</body>
</html>
```